Business Card Design

We need a business card designed for our new company. Prefer a black card with white logo & writing.

Contact Information for Business Card

Ted Galloway, address: 7-4812 Fernhollow Road, Abbotsford, BC, V3K 8R2, Office Phone: 604-712-3390, Cell: 604-947-2164, Email: ted@resinworkshub.ca

Colors

Designer to choose only greyscale colors for use in the design.

```html
<!DOCTYPE html>
<html lang="en">
<head>
<meta charset="utf-8">
<title>Resin Works Hub — Business Card</title>
<link href="https://fonts.googleapis.com/css2?family=Montserrat:wght@300;400;600;800&display=swap" rel="stylesheet">
<style>
  :root {
    --bg: #1e1e1f;
    --card: #232325;
    --card-deep: #1a1a1b;
    --ink: #ffffff;
    --ink-soft: #d9d9d9;
    --grey-mid: #6a6a6c;
  }
  * { box-sizing: border-box; margin: 0; padding: 0; }
  html, body { width: 1200px; height: 711px; overflow: hidden; background: var(--bg); }
  body { font-family: "Montserrat", sans-serif; color: var(--ink); position: relative; }

  .card {
    position: absolute;
    width: 540px;
    height: 309px;
    background: var(--card);
    border-radius: 4px;
    overflow: hidden;
    box-shadow: 0 10px 30px rgba(0,0,0,.45);
  }
  .card--back { left: 40px; top: 201px; }
  .card--front { left: 620px; top: 201px; }

  /* back side */
  .back-pattern {
    position: absolute; inset: 0;
    background: linear-gradient(160deg, #2c2c2e 0%, var(--card-deep) 55%, #2a2a2c 100%);
  }
  .back-brand {
    position: absolute; right: 34px; bottom: 40px;
    display: flex; align-items: center; gap: 8px;
    font-weight: 800; font-size: 15px; letter-spacing: .5px;
  }
  .brand-mark { width: 10px; height: 10px; background: var(--ink); }

  /* front side */
  .front-brand {
    position: absolute; left: 28px; top: 34px;
    display: flex; align-items: center; gap: 10px;
    font-weight: 800; font-size: 24px; line-height: 1; letter-spacing: .5px;
  }
  .front-brand .brand-mark { width: 16px; height: 16px; }

  .contact {
    position: absolute; left: 28px; top: 128px;
    font-weight: 300; font-size: 12.5px; line-height: 1.35;
    color: var(--ink-soft);
  }
  .contact__address { margin-bottom: 16px; }
  .contact__list { list-style: none; }
  .contact__list li { display: flex; align-items: center; gap: 10px; height: 18px; }
  .contact__icon { width: 13px; height: 13px; flex: none; }

  .peak { position: absolute; right: 0; bottom: 0; width: 300px; height: 230px; }

  .person {
    position: absolute; right: 38px; top: 22px;
    text-align: right;
  }
  .person__name { font-size: 26px; line-height: 1.1; white-space: nowrap; }
  .person__first { font-weight: 800; }
  .person__last { font-weight: 300; }
  .person__role { font-weight: 400; font-size: 12px; margin-top: 2px; }
  .accent-bar {
    position: absolute; right: 18px; top: 18px;
    width: 12px; height: 64px; background: var(--ink);
  }
</style>
</head>
<body>

  <section class="card card--back" aria-label="Card back">
    <div class="back-pattern" role="img" aria-label="Repeating embossed mountain-ridge pattern in dark grey"></div>
    <div class="back-brand"><span class="brand-mark"></span>RESIN WORKS HUB</div>
  </section>

  <section class="card card--front" aria-label="Card front">
    <div class="front-brand"><span class="brand-mark"></span>RESIN WORKS HUB</div>

    <div class="contact">
      <p class="contact__address">7-4812 Fernhollow Road,<br>Abbotsford, BC, V3K 8R2.</p>
      <ul class="contact__list">
        <li>
          <svg class="contact__icon" viewBox="0 0 16 16" fill="none" stroke="#fff" stroke-width="1.4"><path d="M3 2h3l1 3-2 1.5a9 9 0 0 0 4.5 4.5L11 9l3 1v3a1 1 0 0 1-1 1A12 12 0 0 1 2 3a1 1 0 0 1 1-1z"/></svg>
          604-712-3390
        </li>
        <li>
          <svg class="contact__icon" viewBox="0 0 16 16" fill="none" stroke="#fff" stroke-width="1.4"><rect x="4" y="1.5" width="8" height="13" rx="1.5"/><circle cx="8" cy="12" r=".8" fill="#fff"/></svg>
          604-947-2164
        </li>
        <li>
          <svg class="contact__icon" viewBox="0 0 16 16" fill="none" stroke="#fff" stroke-width="1.3"><circle cx="8" cy="8" r="6.2"/><ellipse cx="8" cy="8" rx="2.6" ry="6.2"/><path d="M2 8h12"/></svg>
          www.resinworkshub.ca
        </li>
        <li>
          <svg class="contact__icon" viewBox="0 0 16 16" fill="none" stroke="#fff" stroke-width="1.3"><rect x="1.5" y="3.5" width="13" height="9" rx="1"/><path d="M1.5 4l6.5 5 6.5-5"/></svg>
          ted@resinworkshub.ca
        </li>
      </ul>
    </div>

    <svg class="peak" viewBox="0 0 300 230" role="img" aria-label="Snow-capped mountain peak illustration in greyscale">
      <defs>
        <linearGradient id="peakFill" x1="0" y1="0" x2="1" y2="1">
          <stop offset="0" stop-color="#8a8a8c"/>
          <stop offset=".45" stop-color="#3a3a3c"/>
          <stop offset="1" stop-color="#1c1c1d"/>
        </linearGradient>
      </defs>
      <path d="M30 230 C70 170 95 110 120 60 C160 95 220 120 300 130 L300 230 Z" fill="url(#peakFill)"/>
    </svg>

    <div class="accent-bar"></div>
    <div class="person">
      <p class="person__name"><span class="person__first">Ted</span> <span class="person__last">Galloway</span></p>
      <p class="person__role">Owner</p>
    </div>
  </section>

</body>
</html>
```